Website for my photography business

I need a website for my photography business, Bram Kellet Photography. I need a website that has a landing page with a cover photo of each kind of photography I do. For example, Nature, Weddings, Portraits and Architecture. I want it so that when someone comes onto my website they have to choose which kind of photography page they want to visit. So if they click on the wedding photo it will open to a page with my wedding portfolio images and a contact me button. If they choose nature photography I want them to be redirected to an e-commerce section where they can purchase prints. Architecture and Portraits should open up to their respective portfolios with about me and contact info. I like this kind of format because I want people who come to my website for a specific type of photography to be able to be directed there easily without having to look at a mix of other kinds of photography. I will provide a few files to use as placeholders. I have already purchased the bramkelletphotography.example domain name. A Wix website would be great because I am most familiar with it but I am open to anything.

Industry/Entity Type

Photographer

Number of Pages Required

5+ page

Requirements
Must have
• Landing Page and e-commerce

```html
<!DOCTYPE html>
<html lang="en">
<head>
<meta charset="utf-8">
<title>Bram Kellet Photography</title>
<link href="https://fonts.googleapis.com/css2?family=Playfair+Display:wght@400&family=Cormorant+Garamond:ital,wght@1,400&family=Jost:wght@300;400&display=swap" rel="stylesheet">
<style>
  :root {
    --header-bg: #f7f7f7;
    --page-bg: #ffffff;
    --ink: #2b2b2b;
    --ink-soft: #555555;
    --ink-muted: #7a7a7a;
    --icon: #111111;
  }
  * { margin: 0; padding: 0; box-sizing: border-box; }
  html, body { width: 1200px; height: 1031px; overflow: hidden; background: var(--page-bg); }
  .site { position: relative; width: 1200px; height: 1031px; }

  .site-header { position: absolute; left: 0; top: 0; width: 1200px; height: 182px; background: var(--header-bg); }
  .brand-name {
    position: absolute; left: 0; width: 1200px; top: 30px; text-align: center;
    font-family: "Playfair Display", serif; font-weight: 400; font-size: 30px;
    letter-spacing: 2px; color: var(--ink); line-height: 1.2;
  }
  .brand-tag {
    position: absolute; left: 0; width: 1200px; top: 74px; text-align: center;
    font-family: "Jost", sans-serif; font-weight: 300; font-size: 11px;
    letter-spacing: 10px; color: var(--ink-soft); padding-left: 10px; line-height: 1.2;
  }
  .main-nav a {
    position: absolute; top: 126px; transform: translateX(-50%);
    font-family: "Cormorant Garamond", serif; font-style: italic; font-size: 15px;
    color: var(--ink); text-decoration: none; white-space: nowrap; line-height: 1.2;
  }

  .intro {
    position: absolute; left: 0; width: 1200px; top: 205px; text-align: center;
    font-family: "Cormorant Garamond", serif; font-style: italic; font-weight: 400;
    font-size: 27px; color: var(--ink-soft); line-height: 1.2;
  }

  .category-tile { position: absolute; display: block; }
  .tile-architecture { left: 170px; top: 267px; width: 507px; height: 337px;
    background: linear-gradient(180deg, #d9dde0 0%, #b4705a 45%, #c9c2b4 75%, #7fa05a 100%); }
  .tile-portraits { left: 686px; top: 267px; width: 344px; height: 337px;
    background: radial-gradient(ellipse at 55% 50%, #b8b8b8 0%, #7d7d7d 60%, #2a2a2a 100%); }
  .tile-weddings { left: 170px; top: 614px; width: 425px; height: 282px;
    background: radial-gradient(ellipse at 50% 55%, #a89a8a 0%, #7e6e60 55%, #4f4238 100%); }
  .tile-nature { left: 604px; top: 614px; width: 426px; height: 282px;
    background: linear-gradient(180deg, #2f4a2c 0%, #3d5a35 45%, #dfe6ec 72%, #f4f7f9 100%); }

  .social {
    position: absolute; left: 0; width: 1200px; top: 968px;
    display: flex; justify-content: center; gap: 22px;
  }
  .social-link {
    font-family: "Jost", sans-serif; font-weight: 400; font-size: 11px;
    color: var(--icon); text-decoration: none; line-height: 16px; white-space: nowrap;
  }
  .copyright {
    position: absolute; left: 0; width: 1200px; top: 994px; text-align: center;
    font-family: "Jost", sans-serif; font-weight: 300; font-size: 11.5px; color: var(--ink-muted);
    line-height: 1.2;
  }
</style>
</head>
<body>
<div class="site">
  <header class="site-header">
    <div class="brand-name">BRAM KELLET</div>
    <div class="brand-tag">PHOTOGRAPHY</div>
    <nav class="main-nav">
      <a href="#architecture" style="left:260px">Architecture</a>
      <a href="#portraits" style="left:432px">Portraits</a>
      <a href="#weddings" style="left:597px">Weddings</a>
      <a href="#nature" style="left:756px">Nature</a>
      <a href="#book" style="left:930px">Book a Session</a>
    </nav>
  </header>

  <h1 class="intro">Choose your favorite category to discover more</h1>

  <a class="category-tile tile-architecture" href="#architecture" role="img" aria-label="Architecture: modern brick and glass campus building under a pale sky"></a>
  <a class="category-tile tile-portraits" href="#portraits" role="img" aria-label="Portraits: black and white figure study"></a>
  <a class="category-tile tile-weddings" href="#weddings" role="img" aria-label="Weddings: two wedding bands resting on speckled stone"></a>
  <a class="category-tile tile-nature" href="#nature" role="img" aria-label="Nature: red fox sitting on snow before evergreen trees"></a>

  <nav class="social" aria-label="Social links">
    <a class="social-link" href="#linkroom">Linkroom</a>
    <a class="social-link" href="#chatter">Chatter</a>
    <a class="social-link" href="#moodwall">Moodwall</a>
    <a class="social-link" href="#frameshare">Frameshare</a>
  </nav>
  <footer class="copyright">© 2023 by Bram Kellet Photography</footer>
</div>
</body>
</html>
```